BLS Business Card 2018

Larkmere Chiropractic. We have two locations that we want to advertise on the same card. Brightvale OrthoCore campus address: 3815 Pellham Dr., Suite 240, Flowood, MS 39417. Madison address: 246 Willowmere Dr., Building D., Madison, MS 39284. website: www.drlarkmere-example.com. o:(601)555-0147 f:(601)555-0183

Target Market(s)

Health care decision makers: primary care doctors and mothers

Contact Information for Business Card

I have no idea; up for any suggestions and I'd do much better picking from examples versus describing what I'm looking for. We are in a very high end location and would like the cards to look really sharp.

Requirements
Must have
• My name, Martin R Belvane, D.C.

```html
<!DOCTYPE html>
<html lang="en">
<head>
<meta charset="utf-8">
<title>Larkmere Chiropractic – Business Card</title>
<link rel="stylesheet" href="https://fonts.googleapis.com/css2?family=Roboto:wght@400;500&family=Roboto+Condensed:wght@700&display=swap">
<style>
  :root {
    --backdrop: #e6e4e1;
    --card-front: #f4f4f4;
    --card-back: #1b1c1e;
    --ink-dark: #111111;
    --ink-body: #555555;
    --ink-light: #ffffff;
    --rule: #c9c9c9;
    --band-black: #0c0c0c;
    --band-grey: #6a6a6a;
  }
  * { margin: 0; padding: 0; box-sizing: border-box; }
  html, body {
    width: 1200px; height: 960px; overflow: hidden;
    background: var(--backdrop);
    font-family: "Roboto", Arial, sans-serif;
  }
  .canvas { position: relative; width: 1200px; height: 960px; }

  .card { position: absolute; width: 600px; box-shadow: 0 3px 8px rgba(0,0,0,.25); }

  /* Front */
  .card-front { left: 314px; top: 113px; height: 342px; background: var(--card-front); }
  .front-band { position: absolute; left: 0; bottom: 0; width: 600px; height: 22px; }
  .brand-front {
    position: absolute; left: 50px; top: 132px;
    display: flex; align-items: center; gap: 12px;
  }
  .brand-dot { width: 12px; height: 12px; border-radius: 50%; background: var(--ink-dark); }
  .brand-name {
    font-weight: 500; font-size: 24px; line-height: 1.05;
    color: var(--ink-dark); text-transform: uppercase; letter-spacing: .5px;
  }
  .divider {
    position: absolute; left: 308px; top: 57px; width: 2px; height: 216px;
    background: var(--rule);
  }
  .contact { position: absolute; left: 332px; top: 55px; color: var(--ink-body); }
  .doctor-name {
    font-family: "Roboto Condensed", "Arial Narrow", sans-serif;
    font-weight: 700; font-size: 21px; color: var(--ink-dark); margin-bottom: 9px;
  }
  .address { font-size: 14.5px; line-height: 18px; margin-bottom: 7px; }
  .contact-lines { list-style: none; font-size: 14.5px; line-height: 19px; margin-top: 9px; }
  .contact-lines li { display: flex; align-items: center; gap: 8px; }
  .contact-lines svg { width: 14px; height: 14px; fill: var(--ink-dark); flex: none; }

  /* Back */
  .card-back { left: 312px; top: 472px; height: 343px; background: var(--card-back); }
  .brand-back {
    position: absolute; left: 0; right: 0; top: 118px;
    display: flex; justify-content: center; align-items: center; gap: 16px;
  }
  .brand-back .brand-dot { width: 16px; height: 16px; background: var(--ink-light); }
  .brand-back .brand-name { color: var(--ink-light); font-size: 36px; }
  .back-web {
    position: absolute; left: 0; right: 0; top: 282px; text-align: center;
    color: var(--ink-light); font-size: 14px; letter-spacing: 5px; text-transform: uppercase;
  }
</style>
</head>
<body>
<main class="canvas">
  <section class="card card-front">
    <div class="brand-front">
      <span class="brand-dot"></span>
      <div class="brand-name">Larkmere<br>Chiropractic</div>
    </div>
    <div class="divider"></div>
    <div class="contact">
      <h1 class="doctor-name">MARTIN R BELVANE, D.C.</h1>
      <p class="address">Brightvale OrthoCore campus :<br>3815 Pellham Dr., Suite 240<br>Flowood, MS 39417.</p>
      <p class="address">Madison address:<br>246 Willowmere Dr., Building D.<br>Madison, MS 39284.</p>
      <ul class="contact-lines">
        <li><svg viewBox="0 0 16 16"><path d="M3.6 1.2l2.3 2.6-1.3 1.9c.9 2 2.6 3.7 4.6 4.6l1.9-1.3 2.6 2.3-1.5 2.4C7.3 13.6 2.4 8.7 1.2 3.8z"/></svg>(601)555-0147</li>
        <li><svg viewBox="0 0 16 16"><path d="M4 1h8v4H4z M1 6h14v6h-2v-2H3v2H1z M4 11h8v4H4z"/></svg>(601)555-0183</li>
        <li><svg viewBox="0 0 16 16"><path d="M8 1a7 7 0 1 0 0 14A7 7 0 0 0 8 1zm-1 2.2L5 5l1 2-2 1-1-1.5A5 5 0 0 1 7 3.2zM9 13l1-3 2-1 1 1a5 5 0 0 1-4 3z"/></svg>www.drlarkmere-example.com</li>
      </ul>
    </div>
    <svg class="front-band" viewBox="0 0 600 22" preserveAspectRatio="none" aria-hidden="true">
      <polygon points="0,0 392,0 386,22 0,22" fill="var(--band-black)"/>
      <polygon points="392,0 396,0 390,22 386,22" fill="#ffffff"/>
      <polygon points="396,0 600,0 600,22 390,22" fill="var(--band-grey)"/>
    </svg>
  </section>

  <section class="card card-back">
    <div class="brand-back">
      <span class="brand-dot"></span>
      <div class="brand-name">Larkmere<br>Chiropractic</div>
    </div>
    <p class="back-web">www.drlarkmere-example.com</p>
  </section>
</main>
</body>
</html>
```